business card - Helicopter Flight Services, Flight School, etc.

We need a business card design for a new helicopter service.

We offer Helicopter Flight Services, Aerial Filming & Photography, Flight School, and Helicopter Tours. In that order.

Summit BladeAir, Inc.
Dennis Tollerby
SummitBladeair@Kestmail.com
626-418-7352

Based at the Brenwick Airport in Van Nuys, CA. The final design should communicate integrity and safety. Pictures or logos at your discretion.

Card back side - surprise me.

```html
<!DOCTYPE html>
<html lang="en">
<head>
<meta charset="utf-8">
<title>Summit BladeAir, Inc. – Business Card</title>
<link href="https://fonts.googleapis.com/css2?family=Open+Sans:wght@400;600&display=swap" rel="stylesheet">
<style>
  :root {
    --page-bg: #e9e6e1;
    --card-white: #ffffff;
    --ink: #1c1c1c;
    --ink-soft: #2a2a2a;
    --accent-blue: #2f3f9e;
    --band-black: #0a0a0a;
    --sky-top: #3f4aa6;
    --sky-mid: #7c58b0;
    --sky-pink: #d45a7e;
    --sky-low: #f3b48a;
  }
  * { box-sizing: border-box; margin: 0; padding: 0; }
  html, body {
    width: 1200px; height: 902px; overflow: hidden;
    background: var(--page-bg);
    font-family: "Open Sans", Arial, sans-serif;
  }
  .canvas {
    position: relative; width: 1200px; height: 902px;
    display: flex; flex-direction: column; align-items: center; justify-content: center; gap: 40px;
  }
  .card {
    position: relative; width: 700px; height: 400px;
    background: var(--card-white);
    box-shadow: 0 6px 18px rgba(0,0,0,0.18);
    overflow: hidden;
  }
  /* Back side */
  .card-back {
    display: flex; flex-direction: column; align-items: center; justify-content: center;
    color: var(--ink);
  }
  .card-back .company-name { font-size: 60px; font-weight: 400; letter-spacing: 0.5px; }
  .card-back .services { font-size: 28px; font-weight: 400; color: var(--ink-soft); margin-top: 8px; }

  /* Front side */
  .card-front .sky-art { position: absolute; left: 0; top: 0; width: 700px; height: 400px; }
  .card-front .company-name {
    position: absolute; right: 34px; top: 44px;
    font-size: 30px; font-weight: 400; line-height: 1.2; color: var(--ink);
    white-space: nowrap;
  }
  .card-front .person-name {
    position: absolute; right: 34px; top: 150px;
    font-size: 30px; font-weight: 400; color: var(--accent-blue);
    white-space: nowrap;
  }
  .contact-list {
    position: absolute; right: 34px; top: 214px;
    list-style: none; text-align: right;
    font-size: 17px; font-weight: 400; line-height: 27px; color: var(--ink);
  }
  .contact-list li { display: flex; justify-content: flex-end; align-items: center; gap: 10px; white-space: nowrap; }
  .contact-list .icon { width: 16px; height: 16px; flex: none; }
  .contact-list .spacer { width: 16px; flex: none; }
</style>
</head>
<body>
<main class="canvas">
  <section class="card card-back">
    <h1 class="company-name">Summit BladeAir, Inc.</h1>
    <p class="services">Airport, Tour guide, Heliport</p>
  </section>

  <section class="card card-front">
    <svg class="sky-art" viewBox="0 0 700 400">
      <defs>
        <linearGradient id="skyFade" x1="0" y1="0" x2="0" y2="1">
          <stop offset="0" stop-color="var(--sky-top)"/>
          <stop offset="0.45" stop-color="var(--sky-mid)"/>
          <stop offset="0.75" stop-color="var(--sky-pink)"/>
          <stop offset="1" stop-color="var(--sky-low)"/>
        </linearGradient>
      </defs>
      <path role="img" aria-label="Photo of an aircraft climbing into a purple and pink sunset sky"
            d="M0 0 H290 C340 110 345 280 300 400 H0 Z" fill="url(#skyFade)"/>
      <path class="curve-band" d="M290 0 H298 C350 110 358 290 318 400 H300 C345 280 340 110 290 0 Z" fill="var(--band-black)"/>
    </svg>

    <h2 class="company-name">Summit BladeAir, Inc.</h2>
    <p class="person-name">Dennis Tollerby</p>
    <ul class="contact-list">
      <li>626-418-7352
        <svg class="icon" viewBox="0 0 16 16"><rect width="16" height="16" fill="var(--accent-blue)"/><path d="M5 3.5 L7 5.5 L6 7 C6.8 8.6 7.6 9.4 9 10 L10.5 9 L12.5 11 L11 12.5 C7 12 4 9 3.5 5 Z" fill="#fff"/></svg>
      </li>
      <li>SummitBladeair@Kestmail.com
        <svg class="icon" viewBox="0 0 16 16"><rect width="16" height="16" fill="var(--accent-blue)"/><rect x="3" y="4.5" width="10" height="7" fill="none" stroke="#fff" stroke-width="1.2"/><path d="M3 4.5 L8 8.5 L13 4.5" fill="none" stroke="#fff" stroke-width="1.2"/></svg>
      </li>
      <li>2240 W. Larkfield Ave. Ste.B
        <svg class="icon" viewBox="0 0 16 16"><rect width="16" height="16" fill="var(--accent-blue)"/><path d="M8 3 L13 8 H11.5 V12.5 H4.5 V8 H3 Z" fill="#fff"/></svg>
      </li>
      <li>Halden, CA 91820<span class="spacer"></span></li>
    </ul>
  </section>
</main>
</body>
</html>
```